Business card design for holistic health care clinic

We need a double-sided business card design for our holistic health care clinic that integrates our logo design and also its color scheme. My business is called Valmira. It is an integrative medicine clinic. You have already done the logo for me. Please ensure an elegant and upscale design that is not cluttered, but still has all the necessary information (please see below for details).

Target Market(s)

Wellness, fitness, rehabilitation for educated, well-traveled open-minded clients who are focused on natural, organic, balanced and preventive healthcare and lifestyle.

Industry/Entity Type

Medical

Contact Information for Business Card

Modern, clean.

Number of Pages Required

1 page

Font styles to use
Serif
Sans Serif

Colors

Designer to choose colors to be used in the design.

Requirements
Must have
• Logo on one side, all other information on the other side.
• Other information should include:
• Tobias Wrenfeld - DOE, CPT, LMT
• 4100 East Marrow Drive
• Austin, TX 78119
• 512 555 0148
• 818 555 0192
• info@ValmiraHealth.example
• t.wrenfeld@ValmiraHealth.example
Nice to have
• Darker background on front - but not totally black - shaded/dark gray.

```html
<!DOCTYPE html>
<html lang="en">
<head>
<meta charset="utf-8">
<title>Valmira – Business Card</title>
<link href="https://fonts.googleapis.com/css2?family=Nunito:wght@400;600;800&display=swap" rel="stylesheet">
<style>
  :root {
    --page-bg: #e6e4e1;
    --card-bg: #323232;
    --brand-blue: #1b90d4;
    --card-shadow: rgba(0, 0, 0, 0.28);
  }
  * { box-sizing: border-box; margin: 0; padding: 0; }
  html, body {
    width: 1200px;
    height: 780px;
    overflow: hidden;
    background: var(--page-bg);
    font-family: "Nunito", sans-serif;
  }
  .canvas {
    position: relative;
    width: 1200px;
    height: 780px;
    display: flex;
    align-items: center;
    justify-content: center;
    gap: 40px;
  }
  .card {
    position: relative;
    width: 540px;
    height: 309px;
    background: var(--card-bg);
    box-shadow: 0 14px 30px var(--card-shadow);
    color: var(--brand-blue);
  }
  .brand {
    position: absolute;
    display: flex;
    flex-direction: column;
  }
  .brand-name {
    display: flex;
    align-items: center;
    gap: 10px;
    font-weight: 800;
    font-size: 52px;
    line-height: 1;
    letter-spacing: 1px;
    text-transform: uppercase;
  }
  .brand-dot {
    width: 16px;
    height: 16px;
    border-radius: 50%;
    background: var(--brand-blue);
  }
  .brand-tagline {
    margin-top: 6px;
    font-weight: 600;
    font-size: 13px;
    letter-spacing: 0.3px;
  }
  .card-front .brand { left: 186px; top: 150px; }
  .card-back .brand { left: 28px; top: 36px; }
  .card-back .brand-name { font-size: 44px; }
  .card-back .brand-dot { width: 13px; height: 13px; }
  .card-back .brand-tagline { font-size: 11.5px; }

  .address {
    position: absolute;
    left: 28px;
    bottom: 46px;
    font-size: 13px;
    line-height: 1.35;
  }
  .contact-block {
    position: absolute;
    right: 28px;
    bottom: 22px;
    width: 250px;
  }
  .person-name {
    font-weight: 800;
    font-size: 15px;
    text-transform: uppercase;
    letter-spacing: 0.3px;
  }
  .person-title {
    font-size: 12px;
    margin-bottom: 10px;
  }
  .contact-list { list-style: none; }
  .contact-item {
    display: flex;
    align-items: center;
    gap: 8px;
    font-size: 12.5px;
    line-height: 1.6;
  }
  .contact-icon { width: 15px; height: 15px; flex: none; }
</style>
</head>
<body>
<main class="canvas">

  <section class="card card-front" aria-label="Card front">
    <div class="brand">
      <div class="brand-name"><span class="brand-dot"></span>Valmira</div>
      <div class="brand-tagline">Integrative Holistic Medicine</div>
    </div>
  </section>

  <section class="card card-back" aria-label="Card back">
    <div class="brand">
      <div class="brand-name"><span class="brand-dot"></span>Valmira</div>
      <div class="brand-tagline">Integrative Holistic Medicine</div>
    </div>

    <address class="address" style="font-style: normal;">
      4100 East Marrow Drive<br>
      Austin, TX 78119
    </address>

    <div class="contact-block">
      <div class="person-name">Tobias Wrenfeld</div>
      <div class="person-title">DOE, CPT, LMT</div>
      <ul class="contact-list">
        <li class="contact-item">
          <svg class="contact-icon" viewBox="0 0 16 16" aria-hidden="true">
            <circle cx="8" cy="8" r="7.2" fill="none" stroke="currentColor" stroke-width="1.2"/>
            <rect x="5.5" y="3.8" width="5" height="8.4" rx="1" fill="none" stroke="currentColor" stroke-width="1.1"/>
            <circle cx="8" cy="10.7" r="0.6" fill="currentColor"/>
          </svg>
          512 555 0148
        </li>
        <li class="contact-item">
          <svg class="contact-icon" viewBox="0 0 16 16" aria-hidden="true">
            <circle cx="8" cy="8" r="7.2" fill="none" stroke="currentColor" stroke-width="1.2"/>
            <path d="M5.4 4.4c.5-.3 1 .1 1.2.6l.4 1c.1.4-.1.7-.4.9l-.3.2c.3.9 1 1.7 1.9 2.2l.3-.3c.3-.3.6-.4 1-.2l.9.5c.5.3.7.8.3 1.2-.6.7-1.5.9-2.4.4-1.7-.9-2.9-2.3-3.5-4.1-.3-.9 0-1.8.6-2.4z" fill="currentColor"/>
          </svg>
          818 555 0192
        </li>
        <li class="contact-item">
          <svg class="contact-icon" viewBox="0 0 16 16" aria-hidden="true">
            <circle cx="8" cy="8" r="7.2" fill="none" stroke="currentColor" stroke-width="1.2"/>
            <rect x="4" y="5.2" width="8" height="5.6" fill="none" stroke="currentColor" stroke-width="1.1"/>
            <path d="M4 5.4l4 3 4-3" fill="none" stroke="currentColor" stroke-width="1.1"/>
          </svg>
          info@ValmiraHealth.example
        </li>
        <li class="contact-item">
          <svg class="contact-icon" viewBox="0 0 16 16" aria-hidden="true">
            <circle cx="8" cy="8" r="7.2" fill="none" stroke="currentColor" stroke-width="1.2"/>
            <rect x="4" y="5.2" width="8" height="5.6" fill="none" stroke="currentColor" stroke-width="1.1"/>
            <path d="M4 5.4l4 3 4-3" fill="none" stroke="currentColor" stroke-width="1.1"/>
          </svg>
          t.wrenfeld@ValmiraHealth.example
        </li>
      </ul>
    </div>
  </section>

</main>
</body>
</html>
```